New business card/stationary for a consulting company

I am looking for a clean and very professional looking business card for my consulting company as well as corresponding stationary. I am uploading our logo. I like simple and powerful for the feel. No graphics but I am open on everything else. Below is my contact information but would like the final to be in a version I can add my employees information into and print. Thank you.

Daniel Whitcombe
dan@ferncliffadvisory.com
2870 North 9th Avenue, Summit Floor, Elm Ridge, Illinois 60531
www.ferncliffadvisory.com

Industry/Entity Type

Consulting

Contact Information for Business Card

Daniel Whitcombe
dan@ferncliffadvisory.com
www.ferncliffadvisory.com

Font styles to use
Serif
Sans Serif

Requirements
Must have
• Our logo and the business card details.
Nice to have
• our website www.ferncliffadvisory.com

```html
<!DOCTYPE html>
<html lang="en">
<head>
<meta charset="utf-8">
<title>Ferncliff Advisory — Business Card</title>
<link rel="stylesheet" href="https://fonts.googleapis.com/css2?family=Questrial&family=Lora:wght@400;700&display=swap">
<style>
  :root {
    --stage: #000000;
    --navy-deep: #06067e;
    --navy: #12129e;
    --navy-light: #2a2ab4;
    --paper: #ffffff;
    --brand-font: "Questrial", sans-serif;
    --text-font: "Lora", serif;
  }
  * { margin: 0; padding: 0; box-sizing: border-box; }
  html, body {
    width: 1200px; height: 913px; overflow: hidden;
    background: var(--stage);
  }
  .stage { position: relative; width: 1200px; height: 913px; }

  .card {
    position: absolute;
    width: 520px; height: 297px;
    overflow: hidden;
    box-shadow: 0 4px 18px rgba(40, 40, 140, 0.35);
  }

  /* Front face */
  .card--front {
    left: 60px; top: 150px;
    background: linear-gradient(135deg, var(--navy-deep) 0%, var(--navy-light) 45%, var(--navy-deep) 100%);
    color: var(--paper);
  }
  .brand {
    position: absolute;
    display: flex; align-items: center; gap: 12px;
    font-family: var(--brand-font);
    text-transform: uppercase;
    letter-spacing: 0.06em;
  }
  .card--front .brand { left: 60px; top: 96px; font-size: 34px; color: var(--paper); }
  .brand__square { width: 26px; height: 26px; background: currentColor; flex: none; }
  .front__rule {
    position: absolute; left: 0; right: 0; top: 206px;
    height: 2px; background: var(--paper);
  }
  .front__web {
    position: absolute; right: 40px; top: 168px;
    font-family: var(--text-font); font-size: 15px; letter-spacing: 0.02em;
  }

  /* Back face */
  .card--back { left: 620px; top: 466px; background: var(--paper); }
  .card--back .brand { left: 80px; top: 62px; font-size: 30px; color: var(--navy); }
  .back__band {
    position: absolute; left: 0; right: 0; top: 146px; height: 122px;
    background: linear-gradient(135deg, var(--navy-deep) 0%, var(--navy-light) 50%, var(--navy-deep) 100%);
    color: var(--paper);
    font-family: var(--text-font);
  }
  .back__band-rule {
    position: absolute; left: 0; right: 0; top: 108px; height: 2px; background: var(--paper);
  }
  .person {
    position: absolute; left: 26px; top: 14px;
    font-size: 21px; font-weight: 700; letter-spacing: 0.01em;
  }
  .contact-list {
    position: absolute; left: 26px; top: 50px;
    list-style: none; font-size: 12.5px; line-height: 23px;
  }
  .contact-list li, .address { display: flex; align-items: flex-start; gap: 8px; }
  .icon { width: 12px; height: 12px; flex: none; margin-top: 5px; }
  .address {
    position: absolute; left: 270px; top: 18px;
    font-size: 12.5px; line-height: 19px; font-style: normal;
  }
</style>
</head>
<body>
<main class="stage">

  <section class="card card--front" aria-label="Business card front">
    <div class="brand"><span class="brand__square"></span><span>Ferncliff Advisory</span></div>
    <p class="front__web">www.ferncliffadvisory.com</p>
    <div class="front__rule"></div>
  </section>

  <section class="card card--back" aria-label="Business card back">
    <div class="brand"><span class="brand__square"></span><span>Ferncliff Advisory</span></div>
    <div class="back__band">
      <p class="person">Daniel Whitcombe</p>
      <ul class="contact-list">
        <li>
          <svg class="icon" viewBox="0 0 12 12" aria-hidden="true"><rect x="1" y="2.5" width="10" height="7" fill="none" stroke="#fff" stroke-width="1"/><path d="M1 2.5 6 6.5 11 2.5" fill="none" stroke="#fff" stroke-width="1"/></svg>
          <span>dan@ferncliffadvisory.com</span>
        </li>
        <li>
          <svg class="icon" viewBox="0 0 12 12" aria-hidden="true"><circle cx="6" cy="6" r="5" fill="none" stroke="#fff" stroke-width="1"/><ellipse cx="6" cy="6" rx="2.2" ry="5" fill="none" stroke="#fff" stroke-width="0.9"/><path d="M1 6h10" stroke="#fff" stroke-width="0.9"/></svg>
          <span>www.ferncliffadvisory.com</span>
        </li>
      </ul>
      <address class="address">
        <svg class="icon" viewBox="0 0 12 12" aria-hidden="true"><path d="M6 11.5C6 11.5 2 7 2 4.5a4 4 0 0 1 8 0C10 7 6 11.5 6 11.5z" fill="#fff"/><circle cx="6" cy="4.5" r="1.5" fill="#12129e"/></svg>
        <span>2870 North 9th Avenue, Summit Floor,<br>Elm Ridge, Illinois 60531</span>
      </address>
      <div class="back__band-rule"></div>
    </div>
  </section>

</main>
</body>
</html>
```